"Thornbury Accupuncture" needs a Promotional Card - A6 size

Requirements
Must have
• Bright colours, pictures of happy people, acupuncture-related pictures.

```html
<!DOCTYPE html>
<html lang="en">
<head>
<meta charset="utf-8">
<title>Thornbury Accupuncture – Promotional Card</title>
<link href="https://fonts.googleapis.com/css2?family=Source+Sans+3:wght@400;600;700&display=swap" rel="stylesheet">
<style>
  :root {
    --page-bg: #e9e7e4;
    --card-bg: #ffffff;
    --gold: #d6b356;
    --gold-light: #efd48c;
    --gold-pale: #f7e7bd;
    --brand-red: #d8442a;
    --text-grey: #6a6a6a;
    --text-dark: #3c3c3c;
    --skin: #efd3c0;
    --skin-deep: #e2b49c;
    --photo-light: #f8f4f1;
    --garden: #a9b98a;
  }
  * { box-sizing: border-box; margin: 0; padding: 0; }
  html, body { width: 1200px; height: 912px; overflow: hidden; }
  body {
    background: var(--page-bg);
    font-family: "Source Sans 3", "Helvetica Neue", Arial, sans-serif;
    color: var(--text-grey);
    position: relative;
  }
  .card {
    position: absolute;
    width: 497px;
    height: 702px;
    background: var(--card-bg);
    overflow: hidden;
    box-shadow: 0 2px 10px rgba(0,0,0,.12);
  }
  .card--front { left: 90px; top: 88px; }
  .card--back { left: 627px; top: 122px; }

  .photo, .swirl-band { position: absolute; }
  .footer-bar {
    position: absolute; left: 0; bottom: 0; width: 100%; height: 14px;
    background: var(--gold-light);
  }
  .brand-name {
    position: absolute;
    color: var(--brand-red);
    font-weight: 700;
    text-align: center;
    line-height: 1;
  }
  .booking { position: absolute; color: var(--text-dark); }
  .booking .phone { color: var(--brand-red); font-weight: 600; }
  .phone-icon { width: 16px; height: 16px; vertical-align: -2px; margin: 0 3px 0 4px; }

  /* Front */
  .front-photo {
    left: 0; top: 0; width: 497px; height: 297px;
    background:
      radial-gradient(ellipse 45% 55% at 68% 45%, #f3d9c6 0%, rgba(243,217,198,0) 70%),
      radial-gradient(ellipse 50% 30% at 25% 60%, var(--skin-deep) 0%, rgba(226,180,156,0) 75%),
      linear-gradient(180deg, #f4f1ee 0%, #fbfaf9 100%);
  }
  .social-dot {
    position: absolute; left: 18px; top: 24px; width: 42px; height: 42px;
    border-radius: 50%; background: var(--brand-red);
  }
  .front-swirl {
    left: 0; top: 297px; width: 497px; height: 117px;
    background: linear-gradient(180deg, var(--gold-pale) 0%, var(--gold-light) 45%, var(--gold) 100%);
  }
  .front-headline {
    position: absolute; left: 30px; top: 438px; width: 437px;
    text-align: center; font-size: 19px; line-height: 1.3; color: var(--text-grey);
  }
  .front-offer {
    position: absolute; left: 40px; top: 508px; width: 417px;
    text-align: center; font-size: 15px; line-height: 1.27; color: var(--text-grey);
  }
  .front-booking { left: 23px; top: 628px; font-size: 17.5px; line-height: 1.3; }
  .front-brand { right: 20px; top: 628px; font-size: 27px; }

  /* Back */
  .back-photo {
    left: 0; top: 0; width: 497px; height: 220px;
    background:
      radial-gradient(ellipse 60% 45% at 50% 75%, var(--skin) 0%, rgba(239,211,192,0) 75%),
      linear-gradient(180deg, var(--garden) 0%, #dcd4bf 50%, #e9d8c9 100%);
  }
  .back-swirl {
    left: 0; top: 220px; width: 497px; height: 38px;
    background: linear-gradient(180deg, var(--gold-light) 0%, var(--gold) 100%);
  }
  .back-brand { right: 20px; top: 266px; font-size: 27px; }
  .intro {
    position: absolute; left: 24px; top: 347px; width: 450px;
    font-size: 10px; line-height: 1.3; color: var(--text-dark);
  }
  .benefits-title {
    position: absolute; left: 24px; top: 428px;
    font-size: 15.5px; font-weight: 600; color: var(--gold); text-transform: uppercase;
  }
  .benefits {
    position: absolute; left: 24px; top: 452px; list-style: none;
    font-size: 14.5px; color: var(--text-dark);
  }
  .benefits li { display: flex; align-items: center; height: 24px; }
  .bullet { width: 11px; height: 11px; margin-right: 7px; }
  .treatment-photo { left: 350px; width: 120px; height: 82px; }
  .treatment-photo--one {
    top: 417px;
    background: radial-gradient(ellipse 55% 60% at 55% 55%, var(--skin) 0%, var(--photo-light) 85%);
  }
  .treatment-photo--two {
    top: 504px;
    background: radial-gradient(ellipse 70% 70% at 45% 60%, var(--skin-deep) 0%, #f4ddd0 90%);
  }
  .treatment-photo--three {
    top: 591px;
    background: linear-gradient(160deg, #f5efe9 0%, #dfbea6 60%, #c99a7d 100%);
  }
  .practitioner-photo {
    left: 19px; top: 582px; width: 88px; height: 106px;
    background: linear-gradient(180deg, #f4f2f0 0%, #c9a592 45%, #9a6a86 100%);
  }
  .practitioner {
    position: absolute; left: 117px; top: 600px;
    font-size: 14.5px; line-height: 1.22; color: var(--gold); font-weight: 400;
  }
  .back-booking { left: 117px; top: 641px; font-size: 13.5px; line-height: 1.25; }
</style>
</head>
<body>

<svg width="0" height="0" style="position:absolute">
  <defs>
    <symbol id="phone-icon" viewBox="0 0 16 16">
      <circle cx="8" cy="8" r="7" fill="none" stroke="#d8442a" stroke-width="1.6"/>
      <path d="M5.4 4.3l1.4-.2.8 2-1 .8c.5 1.1 1.3 1.9 2.4 2.4l.8-1 2 .8-.2 1.4c-3.3.3-6.5-2.9-6.2-6.2z" fill="#d8442a"/>
    </symbol>
    <symbol id="chevron-bullet" viewBox="0 0 12 12">
      <circle cx="6" cy="6" r="6" fill="#efd48c"/>
      <path d="M5 3.5L7.5 6 5 8.5" fill="none" stroke="#fff" stroke-width="1.5"/>
    </symbol>
  </defs>
</svg>

<!-- Front of card -->
<section class="card card--front">
  <div class="photo front-photo" role="img" aria-label="Photo of a smiling woman lying down receiving acupuncture needles on her back"></div>
  <div class="social-dot" aria-hidden="true"></div>
  <div class="swirl-band front-swirl" role="img" aria-label="Flowing gold swirl ornament"></div>

  <p class="front-headline">Acupuncture improves the well-being and contribute to physical and emotional balance.</p>
  <p class="front-offer">Come recive a stress reducing<br>Acupuncture treatment from<br>Mira Delacourt, Thornbury Accupuncture</p>

  <p class="booking front-booking">Call <svg class="phone-icon"><use href="#phone-icon"/></svg><span class="phone">07700 900461</span><br>to book your appointment</p>
  <p class="brand-name front-brand">Thornbury<br>Accupuncture</p>
  <div class="footer-bar"></div>
</section>

<!-- Back of card -->
<section class="card card--back">
  <div class="photo back-photo" role="img" aria-label="Photo of a happy three-generation family laughing together on a sofa outdoors"></div>
  <div class="swirl-band back-swirl" role="img" aria-label="Flowing gold swirl ornament"></div>
  <p class="brand-name back-brand">Thornbury<br>Accupuncture</p>

  <p class="intro">The term “acupuncture” describes a family of procedures involving the stimulation of points on the body using a variety of techniques. The acupuncture technique that has been most often studied scientifically involves penetrating the skin with thin, solid, metallic needles that are manipulated by the hands or by electrical stimulation.</p>

  <h2 class="benefits-title">How Acupuncure Works</h2>
  <ul class="benefits">
    <li><svg class="bullet"><use href="#chevron-bullet"/></svg>Releases Endorphins</li>
    <li><svg class="bullet"><use href="#chevron-bullet"/></svg>Balancing Neurotransmitters</li>
    <li><svg class="bullet"><use href="#chevron-bullet"/></svg>Regulates Immune System</li>
    <li><svg class="bullet"><use href="#chevron-bullet"/></svg>Improving Circulatio</li>
  </ul>

  <div class="photo treatment-photo treatment-photo--one" role="img" aria-label="Photo of a relaxed woman receiving facial acupuncture"></div>
  <div class="photo treatment-photo treatment-photo--two" role="img" aria-label="Photo of hands placing acupuncture needles on a back"></div>
  <div class="photo treatment-photo treatment-photo--three" role="img" aria-label="Photo of a woman lying face down during a treatment"></div>

  <div class="photo practitioner-photo" role="img" aria-label="Portrait photo of the acupuncture practitioner"></div>
  <p class="practitioner">Mira Delacourt<br>Thornbury Accupuncture</p>
  <p class="booking back-booking">Call <svg class="phone-icon"><use href="#phone-icon"/></svg><span class="phone">07700 900461</span><br>to book your appointment</p>
  <div class="footer-bar"></div>
</section>

</body>
</html>
```